Packaging and labelling for Swiss made Organic CBD Oil

Visit our website www.clearleafmerida.example
We have not put any product on yet as require packaging and label design .
Website will give you a great feel for the company and how we have used
the logo . The Vextora cbd product shown is a company similar to ourselves with similar core values , we liked the clean packaging design they have .

Im happy if you want use the mandala symbol in our logo separate from
KELVORA, to separate and use the mandala symbol as a larger icon than
it appears in our logo
Clean , Pure , organic feel. Like the product to look pharmaceutical and life changing not gimmicky.
Colours to go with or be the same as our logo colours
But not too cold and clinical
Bottle size 84mm x 25mm
Label size 75mm x 30mm
Box 30mm x 30mm x 100mm
6 products
Full Spectrum :
500mg CBD (5%)
1000mg CBD ( 10% )
1500mg CBD (15%)
2000mg CBD ( 20% )
Broad spectrum THC Free
500mg CBD (5%)
Pets
500mg Broad Spectrum THC Free
Updates

Would like the design to be more modern than traditional

LABEL Information Front of Bottle - Logo KELVORA & Mandala - Mandala can be used separately as design symbol Organic Cannabis Oil 1500mg CBD (15%) Ful Spectrum 10ml Back of bottle Ingredients: Organic Cannabis Oil Extract Organic Sunflower Seed Oil THC - 0.2% Certified Swiss Organic Cultivation Shake well before use. Store in a cool , dry place and out of the each of children BOX information Front and rear Logo - KELVORA & Mandala - Mandala can be used separately as a design symbol Organic Cannabis Oil 1500mg CBD (15%) Full Spectrum Sides x 2 This product is a food supplement and is not intended to diagnose, treat, cure or prevent any disease If you are pregnant, lactating or taking any medication consult your health care practitioner Suitable for vegetarians and vegans Ingredients Organic Cannabis Oil extract Organis Sunflower Oil Store in a cool ,dry place, out of the reach of children Recommended Use 1-5 drops ( 1 drop = 7.5mg CBD ) Subject to body weight and personal requirement - visit www.clearleafmerida for more information 100% Natural 100% Organic GMO free 100% Vegan ( symbol with each ) Expiry date see bottle label Cultivated and manufactured in Switzerland

Target Market(s)

age 40 - 80

Font styles to use
Other font styles liked:
• In our website we have used Open Sans for the copy and Lato for headings .

Requirements
Must have
• look like an Industry leader
Kelvora will change the quality of peoples lives and in some cases may
even save lives so want look powerful and credible
Our Mission is - Through Delivering Pure , Premium , Organic products we will educate, inform and help people achieve healthier , happier lifestyles
Nice to have
• Colours to look good with our logo colours or be the same as our logo
colours
Logo Font - Avenir Black and Avenir Book

Font used in website - Content - Open Sans / Headings - Lato
If you have another font for the packaging information that will go well with
our logo, I'm happy for you to use your skills

```html
<!DOCTYPE html>
<html lang="en">
<head>
<meta charset="utf-8">
<title>Kelvora Organic Cannabis Oil – Label and Box Dieline</title>
<link href="https://fonts.googleapis.com/css2?family=Questrial&family=Open+Sans:wght@400;700&display=swap" rel="stylesheet">
<style>
  :root {
    --paper: #ffffff;
    --ink: #8a8a8a;
    --ink-soft: #9a9a9a;
    --teal: #7fd0cc;
    --teal-faint: #e3f4f3;
    --tag: #e8f5f4;
    --cut: #c9c9c9;
    --fold: #8ad9d5;
  }
  * { box-sizing: border-box; margin: 0; padding: 0; }
  html, body { width: 1200px; height: 1000px; overflow: hidden; background: var(--paper); }
  .canvas { position: relative; width: 1200px; height: 1000px; background: var(--paper); color: var(--ink); font-family: "Open Sans", sans-serif; }

  .dieline { position: absolute; border: 1px solid var(--cut); background: var(--paper); overflow: hidden; }
  .fold-guide { position: absolute; top: 42px; width: 2px; height: 915px; background: var(--fold); z-index: 5; }

  .watermark { position: absolute; border-radius: 50%;
    background: radial-gradient(circle, rgba(127,208,204,0.16) 0%, rgba(127,208,204,0.08) 55%, rgba(127,208,204,0) 72%); }

  .panel { position: absolute; top: 0; height: 100%; width: 166px; }
  .centered { position: absolute; left: 0; width: 100%; text-align: center; }

  .brand { font-family: "Questrial", sans-serif; font-size: 23px; letter-spacing: 1px; color: #7b7b7b; display: flex; align-items: center; justify-content: center; gap: 5px; }
  .brand-dot { width: 8px; height: 8px; border-radius: 50%; background: var(--teal); }

  .product-name { font-family: "Questrial", sans-serif; font-size: 23px; line-height: 22px; color: var(--ink); }
  .strength { font-family: "Questrial", sans-serif; font-size: 18px; line-height: 21px; color: var(--ink); }
  .spectrum { font-family: "Questrial", sans-serif; font-size: 16px; color: var(--ink); }
  .spectrum-tag { display: inline-block; background: var(--tag); padding: 0 5px; line-height: 19px; }
  .volume { font-family: "Questrial", sans-serif; font-size: 13px; color: var(--ink); }

  .fine-print { font-size: 9.5px; line-height: 11.6px; color: var(--ink-soft); padding: 0 8px; }
  .fine-print p + p { margin-top: 8px; }
  .fine-print strong { font-weight: 700; }
  .fine-print .accent { color: var(--teal); font-weight: 700; }

  .claim-icon { position: absolute; left: 58px; width: 50px; height: 50px; }
  .claim-label { font-size: 9px; font-weight: 700; color: var(--teal); }
</style>
</head>
<body>
<main class="canvas">

  <!-- Bottle label 75 x 30 mm -->
  <section class="dieline bottle-label" style="left:167px; top:484px; width:166px; height:413px;">
    <div class="watermark" role="img" aria-label="Faint large brand emblem decoration" style="left:-10px; top:100px; width:186px; height:186px;"></div>
    <div class="centered brand" style="top:42px;"><span class="brand-dot"></span>KELVORA</div>
    <div class="centered product-name" style="top:165px; font-size:25px; line-height:26px;">ORGANIC<br>CANNABIS<br>OIL</div>
    <div class="centered strength" style="top:287px; line-height:19px;">1500 mg<br>CBD (5%)</div>
    <div class="centered spectrum" style="top:341px; font-size:18px;">Full Spectrum</div>
    <div class="centered volume" style="top:393px;">10 ml</div>
  </section>

  <!-- Box lid -->
  <section class="dieline box-lid" style="left:703px; top:50px; width:332px; height:331px;">
    <div class="watermark" role="img" aria-label="Large brand emblem centred on the lid" style="left:76px; top:75px; width:180px; height:180px; background: radial-gradient(circle, rgba(127,208,204,0.35) 0%, rgba(127,208,204,0.18) 50%, rgba(127,208,204,0) 72%);"></div>
  </section>

  <!-- Box wrap 30 x 30 x 100 mm -->
  <section class="dieline box-wrap" style="left:373px; top:398px; width:662px; height:552px;">
    <div class="watermark" role="img" aria-label="Faint large brand emblem spanning front and side panels" style="left:-20px; top:60px; width:450px; height:450px;"></div>
    <div class="watermark" role="img" aria-label="Faint brand emblem edge on rear side panel" style="left:570px; top:200px; width:160px; height:160px;"></div>

    <!-- Front panel -->
    <div class="panel front-panel" style="left:0;">
      <div class="centered brand" style="top:45px;"><span class="brand-dot"></span>KELVORA</div>
      <div class="centered product-name" style="top:261px;">ORGANIC<br>CANNABIS<br>OIL</div>
      <div class="centered strength" style="top:398px;">1500 mg<br>CBD (5%)</div>
      <div class="centered spectrum" style="top:507px;"><span class="spectrum-tag">Full Spectrum</span></div>
    </div>

    <!-- Side panel: information -->
    <div class="panel side-panel" style="left:166px;">
      <div class="centered fine-print" style="top:338px;">
        <p>This product is a food supplement and is not intended to diagnose, treat, cure or prevent any disease.</p>
        <p>If you are pregnant, lactating or taking any medication consult your health care practitioner.</p>
        <p>Suitable for vegetarians and vegans.</p>
        <p><strong>Ingredients:</strong> Organic Cannabis Oil Extract Organic Sunflower Oil Store in a cool, dry place, out of the reach of children.</p>
      </div>
    </div>

    <!-- Rear panel -->
    <div class="panel front-panel" style="left:331px;">
      <div class="centered brand" style="top:45px;"><span class="brand-dot"></span>KELVORA</div>
      <div class="centered product-name" style="top:261px;">ORGANIC<br>CANNABIS<br>OIL</div>
      <div class="centered strength" style="top:398px;">1500 mg<br>CBD (5%)</div>
      <div class="centered spectrum" style="top:507px;"><span class="spectrum-tag">Full Spectrum</span></div>
    </div>

    <!-- Side panel: usage and claims -->
    <div class="panel usage-panel" style="left:497px;">
      <div class="centered fine-print" style="top:49px; padding:0 4px;">
        <span class="accent">Recommended Use:</span><br>
        1-5 drops (1 drop = 7.5mg CBD) Subject to body weight and personal requirement – visit www.clearleafmerida.example for more information.
      </div>

      <svg class="claim-icon" style="top:144px;" viewBox="0 0 50 50" role="img" aria-label="100% Natural claim icon">
        <circle cx="25" cy="25" r="23" fill="none" stroke="var(--teal)" stroke-width="2"/>
        <circle cx="25" cy="25" r="14" fill="var(--teal)" opacity="0.8"/>
      </svg>
      <div class="centered claim-label" style="top:197px;">100% Natural</div>

      <svg class="claim-icon" style="top:226px;" viewBox="0 0 50 50" role="img" aria-label="100% Organic claim icon">
        <circle cx="25" cy="25" r="23" fill="none" stroke="var(--teal)" stroke-width="2"/>
        <circle cx="25" cy="25" r="14" fill="var(--teal)" opacity="0.8"/>
      </svg>
      <div class="centered claim-label" style="top:279px;">100% Organic</div>

      <svg class="claim-icon" style="top:310px;" viewBox="0 0 50 50" role="img" aria-label="100% Vegan claim icon">
        <circle cx="25" cy="25" r="23" fill="none" stroke="var(--teal)" stroke-width="2"/>
        <circle cx="25" cy="25" r="14" fill="var(--teal)" opacity="0.8"/>
      </svg>
      <div class="centered claim-label" style="top:364px;">100% Vegan</div>

      <svg class="claim-icon" style="top:394px;" viewBox="0 0 50 50" role="img" aria-label="GMO Free claim icon">
        <circle cx="25" cy="25" r="23" fill="none" stroke="var(--teal)" stroke-width="2"/>
        <circle cx="25" cy="25" r="14" fill="var(--teal)" opacity="0.8"/>
      </svg>
      <div class="centered claim-label" style="top:448px;">GMO Free</div>

      <div class="centered fine-print" style="top:484px;">Expiry date see bottle label.</div>
      <div class="centered fine-print" style="top:504px;">Cultivated and manufactured in Switzerland.</div>
    </div>
  </section>

  <!-- Fold guides -->
  <div class="fold-guide" style="left:538px;"></div>
  <div class="fold-guide" style="left:868px;"></div>

</main>
</body>
</html>
```